Allied Health team of Physiotherapists & Occupational Therapists seek a business card design

We have our new logo, we now need our new business cards and stationary. Tidewell: Oedema & Family Clinic is seeking a generic card design to represent our whole team and individual cards for each therapist that incorporates our new logo to communicate our holistic approach that is calming, nuturing, supportive and welcoming.
Our Physiotherapists and Occupational Therapists assess, treat and provide education for people who are at risk of or who have lymphoedema. This is often as a result of treatment for cancer. We provide pre-operative and post-operative management and cancer rehabilitation in our Pilates studio. Our team also consists of Physiotherapists who have a strong interest in pelvic floor and continence management for both men and women.

Target Market(s)

Mainly women health conscious

Industry/Entity Type

Allied Health: Physiotherapy / Occupational Therapy

Contact Information for Business Card

Address: 14 Gallivant Ave Frankston 3199 Phone: 84316570 fax: 8431 6578 Email: info@tidewellcareservices.com.au Website: tidewellcareservices.com.au Facebook address: facebook.com/TidewellOedemaAndFamilyCareClinic. Room to write appointments. Individual cards need to have name, office email and individual email and professional details

Requirements
Must have
• Logo as per uploaded documents

```html
<!DOCTYPE html>
<html lang="en">
<head>
<meta charset="utf-8">
<title>Tidewell: Oedema &amp; Family Clinic — Business Card</title>
<link rel="stylesheet" href="https://fonts.googleapis.com/css2?family=Arimo:wght@400&display=swap">
<style>
  :root {
    --page: #efefed;
    --peach: #f8af80;
    --sage: #c5ccc3;
    --frost: #e6e5e2;
    --ink: #2e2e2e;
    --ink-soft: #555555;
    --white: #ffffff;
  }
  * { margin: 0; padding: 0; box-sizing: border-box; }
  html, body {
    width: 1200px;
    height: 961px;
    overflow: hidden;
    background: var(--page);
    font-family: "Arimo", Arial, sans-serif;
  }
  .card {
    position: absolute;
    left: 50px;
    top: 161px;
    width: 1100px;
    height: 638px;
    overflow: hidden;
    box-shadow: 0 6px 24px rgba(0,0,0,0.12);
  }
  .card-backdrop {
    position: absolute;
    inset: 0;
    background: linear-gradient(160deg,
      var(--peach) 0%,
      var(--peach) 50%,
      var(--sage) 62%,
      var(--frost) 74%,
      var(--frost) 100%);
  }
  .brand {
    position: absolute;
    left: 68px;
    top: 64px;
    width: 220px;
    height: 220px;
    display: flex;
    align-items: center;
    justify-content: center;
  }
  .brand-ring {
    position: absolute;
    inset: 0;
    border: 2px solid var(--white);
    border-radius: 50%;
  }
  .brand-name {
    position: relative;
    color: var(--white);
    font-size: 40px;
    font-weight: 400;
  }
  .person {
    position: absolute;
    left: 73px;
    top: 356px;
    color: var(--ink);
  }
  .person-name {
    font-size: 43px;
    line-height: 1;
    letter-spacing: 0.5px;
  }
  .person-title {
    margin-top: 12px;
    font-size: 28px;
    line-height: 1;
  }
  .address {
    position: absolute;
    right: 49px;
    top: 381px;
    text-align: right;
    font-style: normal;
    color: var(--ink-soft);
    font-size: 23px;
    line-height: 27px;
  }
  .contacts {
    position: absolute;
    right: 50px;
    top: 462px;
    list-style: none;
    color: var(--ink-soft);
    font-size: 22px;
  }
  .contact-row {
    display: flex;
    align-items: center;
    justify-content: flex-end;
    height: 37px;
    gap: 16px;
  }
  .contact-icon {
    width: 22px;
    height: 22px;
    fill: none;
    stroke: var(--ink);
    stroke-width: 1.8;
  }
</style>
</head>
<body>
  <main class="card">
    <div class="card-backdrop" role="img" aria-label="Decorative wave background in peach and sage fading to a light frosted tone"></div>

    <div class="brand">
      <span class="brand-ring"></span>
      <span class="brand-name">Tidewell</span>
    </div>

    <div class="person">
      <p class="person-name">JHON SMITH</p>
      <p class="person-title">YOUR TITLE</p>
    </div>

    <address class="address">
      482 Brindlecove Rd Ashgrove,<br>VA, US
    </address>

    <ul class="contacts">
      <li class="contact-row">
        <span>123 456 7890</span>
        <svg class="contact-icon" viewBox="0 0 24 24" aria-label="Phone"><path d="M6 3l3 4-2 2c1 3 4 6 7 7l2-2 4 3-2 3C11 20 4 13 3 5z"/></svg>
      </li>
      <li class="contact-row">
        <span>123 465 7890</span>
        <svg class="contact-icon" viewBox="0 0 24 24" aria-label="Mobile"><rect x="7" y="2" width="10" height="20" rx="1.5"/><line x1="11" y1="18.5" x2="13" y2="18.5"/></svg>
      </li>
      <li class="contact-row">
        <span>hello@uremail.com</span>
        <svg class="contact-icon" viewBox="0 0 24 24" aria-label="Email"><rect x="2" y="6" width="20" height="12"/><path d="M2 6l10 7 10-7M2 18l8-6M22 18l-8-6"/></svg>
      </li>
      <li class="contact-row">
        <span>www.urwebsite.com</span>
        <svg class="contact-icon" viewBox="0 0 24 24" aria-label="Website"><circle cx="12" cy="12" r="10"/><ellipse cx="12" cy="12" rx="4.5" ry="10"/><line x1="2" y1="12" x2="22" y2="12"/><path d="M4 7h16M4 17h16"/></svg>
      </li>
    </ul>
  </main>
</body>
</html>
```